"Harbor Builders" is a residential building company and needs a new business card design and may re

We would like a redesign based on the existing logo, and would like to see a new font as well. We are bespoke home builders who build sustainable energy efficient homes.

Industry/Entity Type

Construction

Contact Information for Business Card

Business card size 40mm x 90mm

Colors

Designer to choose colors to be used in the design.

```html
<!DOCTYPE html>
<html lang="en">
<head>
<meta charset="utf-8">
<title>Harbor Builders – Business Card</title>
<link rel="stylesheet" href="https://fonts.googleapis.com/css2?family=Source+Sans+3:wght@400;600;700&family=PT+Sans+Narrow:wght@400;700&display=swap">
<style>
  :root {
    --page-bg: #9b9b9b;
    --card-light: #dcdcde;
    --brand-green: #a4b72a;
    --ink: #161616;
    --ink-soft: #4a4a4c;
    --divider: #9a9a9c;
    --white: #ffffff;
  }
  * { box-sizing: border-box; margin: 0; padding: 0; }
  html, body { width: 1105px; height: 1200px; overflow: hidden; }
  body {
    background: var(--page-bg);
    font-family: "Source Sans 3", Arial, sans-serif;
    position: relative;
  }
  .card {
    position: absolute;
    left: 182px;
    width: 747px;
    height: 426px;
    overflow: hidden;
  }
  .card--front { top: 119px; background: var(--card-light); }
  .card--back { top: 636px; background: var(--brand-green); }

  /* front: brand */
  .brand {
    position: absolute;
    left: 240px;
    top: 300px;
    display: flex;
    align-items: center;
    gap: 14px;
  }
  .card--front .brand { left: 52px; top: 180px; }
  .brand__mark {
    width: 34px; height: 34px;
    background: var(--brand-green);
  }
  .brand__name {
    font-weight: 600;
    font-size: 34px;
    color: var(--ink);
    letter-spacing: 0.2px;
    line-height: 1;
  }
  .divider {
    position: absolute;
    left: 373px; top: 112px;
    width: 2px; height: 200px;
    background: var(--divider);
  }

  /* front: contact */
  .contact {
    position: absolute;
    left: 404px; top: 112px;
    color: var(--ink-soft);
  }
  .contact__name {
    font-weight: 700;
    font-size: 26px;
    color: var(--ink);
    line-height: 1;
    margin-bottom: 14px;
  }
  .contact__company {
    font-weight: 700;
    font-size: 16.5px;
    line-height: 22px;
  }
  .contact__address {
    font-size: 17.5px;
    line-height: 22px;
    margin-bottom: 10px;
  }
  .contact__row {
    display: flex;
    align-items: center;
    gap: 10px;
    font-size: 17.5px;
    line-height: 24px;
  }
  .contact__icon { width: 16px; display: flex; justify-content: center; }
  .contact__legal {
    font-family: "PT Sans Narrow", Arial Narrow, sans-serif;
    font-size: 15px;
    margin-top: 6px;
  }
  .contact__legal b { font-weight: 700; }

  /* front: footer band */
  .footer-band {
    position: absolute;
    left: 0; bottom: 0;
    width: 747px; height: 44px;
  }
  .footer-band__url {
    position: absolute;
    right: 20px; bottom: 9px;
    color: var(--white);
    font-weight: 600;
    font-size: 16px;
    letter-spacing: 1.2px;
  }

  /* back */
  .card--back .brand {
    left: 50%; top: 170px;
    transform: translateX(-50%);
    gap: 18px;
  }
  .card--back .brand__mark { width: 46px; height: 46px; background: var(--ink); }
  .card--back .brand__name { font-size: 50px; }
  .back-url {
    position: absolute;
    left: 0; right: 0; top: 355px;
    text-align: center;
    font-weight: 700;
    font-size: 17px;
    letter-spacing: 3.4px;
    color: var(--ink);
  }
</style>
</head>
<body>
  <section class="card card--front" aria-label="Business card front">
    <div class="brand">
      <span class="brand__mark"></span>
      <span class="brand__name">harbor builders</span>
    </div>

    <div class="divider"></div>

    <div class="contact">
      <p class="contact__name">Daniel Ferrante</p>
      <p class="contact__company">Harbor Builders Pty Ltd</p>
      <p class="contact__address">PO Box 4120 Eastgate<br>LPO Bayview WA 6099</p>
      <p class="contact__row">
        <span class="contact__icon">
          <svg width="11" height="18" viewBox="0 0 11 18" aria-hidden="true">
            <rect x="0.75" y="0.75" width="9.5" height="16.5" rx="1.5" fill="none" stroke="var(--ink)" stroke-width="1.5"/>
            <rect x="2.5" y="2.8" width="6" height="10" fill="var(--ink)"/>
          </svg>
        </span>
        0400 555 018
      </p>
      <p class="contact__row">
        <span class="contact__icon">
          <svg width="14" height="10" viewBox="0 0 14 10" aria-hidden="true">
            <rect width="14" height="10" fill="var(--ink)"/>
            <path d="M0.5 0.8 L7 5.6 L13.5 0.8" fill="none" stroke="var(--card-light)" stroke-width="1.3"/>
          </svg>
        </span>
        daniel@harborbuilders.com.au
      </p>
      <p class="contact__legal"><b>Registration:</b> 40218 &nbsp;<b>ABN:</b> 55 204 918 337</p>
    </div>

    <div class="footer-band">
      <svg width="747" height="44" viewBox="0 0 747 44" aria-hidden="true">
        <rect x="0" y="26" width="420" height="18" fill="var(--brand-green)"/>
        <polygon points="392,44 432,8 747,8 747,44" fill="var(--white)"/>
        <polygon points="402,44 440,10 747,10 747,44" fill="var(--ink)"/>
      </svg>
      <span class="footer-band__url">www.harborbuilders.com.au</span>
    </div>
  </section>

  <section class="card card--back" aria-label="Business card back">
    <div class="brand">
      <span class="brand__mark"></span>
      <span class="brand__name">harbor builders</span>
    </div>
    <p class="back-url">WWW.HARBORBUILDERS.COM.AU</p>
  </section>
</body>
</html>
```